Building company buisness cards

We are looking for a sharp modern new look for our business cards.
We are a New Zealand based company that specialises in house and land packages.
We have attached a photo of the current logo and would like to see if it can be improved somehow if needed.
We are open to any colours but we have chosen green at this stage.
Feel free to change the font and make the logo smarter looking.
Play with the colours and see what looks best.

We want a card that looks so good know one will want to throw it away!

Target Market(s)

Home buyers

Industry/Entity Type

Building

Contact Information for Business Card

Derek Tolvane
0217394062
dtolvane@quillmarkhomesteads.co.nz
quillmarkhomesteads.co.nz

Font styles to use
Serif
Sans Serif

Colors

Designer to choose colors to be used in the design.

Requirements
Must have
• Logo and company name on one side, details on the other side
Nice to have
• Color codes for the original green are HEX #4a8028, RGB(74,128,40), CMYK(42,0,69,50)
• Round corners, Raised and/or spot UV

```html
<!DOCTYPE html>
<html lang="en">
<head>
<meta charset="utf-8">
<title>Quillmark Homesteads – Business Cards</title>
<link href="https://fonts.googleapis.com/css2?family=Open+Sans:wght@400;600&display=swap" rel="stylesheet">
<style>
  :root {
    --brand-green: #4a8028;
    --brand-green-bright: #4f9a22;
    --card-white: #ffffff;
    --ink-grey: #4a4a4a;
    --backdrop: #2b2b2b;
  }
  * { box-sizing: border-box; margin: 0; padding: 0; }
  html, body {
    width: 1200px;
    height: 885px;
    overflow: hidden;
    background: var(--backdrop);
    font-family: "Open Sans", Arial, sans-serif;
  }
  .stage { position: relative; width: 1200px; height: 885px; }
  .card {
    position: absolute;
    width: 560px;
    height: 311px;
    background: var(--card-white);
    border-radius: 4px;
    box-shadow: 0 14px 30px rgba(0,0,0,0.45);
    overflow: hidden;
  }
  .card--front { left: 60px; top: 110px; }
  .card--back  { left: 580px; top: 470px; }

  .company-name {
    color: var(--brand-green-bright);
    font-weight: 600;
    white-space: nowrap;
  }

  /* front */
  .card--front .company-name {
    position: absolute;
    left: 0; right: 0;
    top: 118px;
    text-align: center;
    font-size: 32px;
  }
  .website {
    position: absolute;
    left: 0; right: 0;
    bottom: 40px;
    text-align: center;
    color: var(--ink-grey);
    font-size: 15px;
    letter-spacing: 4px;
  }

  /* back */
  .roof-band {
    position: absolute;
    left: 0; top: 0;
    width: 560px;
    height: 311px;
  }
  .roof-band path {
    fill: none;
    stroke: var(--brand-green);
    stroke-width: 40;
    stroke-linejoin: round;
  }
  .contact {
    position: absolute;
    right: 22px;
    top: 22px;
    list-style: none;
    color: var(--ink-grey);
    font-size: 13px;
    line-height: 1.7;
  }
  .contact__item { display: flex; justify-content: flex-end; align-items: center; gap: 8px; }
  .contact__icon { width: 12px; height: 12px; fill: var(--brand-green); flex: none; }
  .holder-name {
    position: absolute;
    left: 36px;
    top: 120px;
    color: var(--brand-green-bright);
    font-weight: 600;
    font-size: 21px;
    letter-spacing: 0.3px;
    text-transform: uppercase;
  }
  .card--back .company-name {
    position: absolute;
    right: 28px;
    bottom: 70px;
    font-size: 26px;
  }
</style>
</head>
<body>
<main class="stage">
  <section class="card card--front" aria-label="Card front">
    <h1 class="company-name">Quillmark Homesteads</h1>
    <p class="website">www.quillmarkhomesteads.co.nz</p>
  </section>

  <section class="card card--back" aria-label="Card back">
    <svg class="roof-band" viewBox="0 0 560 311" aria-hidden="true">
      <path d="M150 340 L225 140 Q235 116 262 116 L600 122"/>
    </svg>
    <ul class="contact">
      <li class="contact__item">
        <span>0217394062</span>
        <svg class="contact__icon" viewBox="0 0 24 24" aria-hidden="true"><path d="M6.6 10.8a15.1 15.1 0 0 0 6.6 6.6l2.2-2.2a1 1 0 0 1 1-.25 11.4 11.4 0 0 0 3.6.57 1 1 0 0 1 1 1V20a1 1 0 0 1-1 1A17 17 0 0 1 3 4a1 1 0 0 1 1-1h3.5a1 1 0 0 1 1 1c0 1.25.2 2.45.57 3.57a1 1 0 0 1-.25 1z"/></svg>
      </li>
      <li class="contact__item">
        <span>dtolvane@quillmarkhomesteads.co.nz</span>
        <svg class="contact__icon" viewBox="0 0 24 24" aria-hidden="true"><path d="M2 5h20v14H2z M2 5l10 8 10-8" fill="var(--brand-green)" stroke="#fff" stroke-width="1.5"/></svg>
      </li>
    </ul>
    <h2 class="holder-name">Derek Tolvane</h2>
    <p class="company-name">Quillmark Homesteads</p>
  </section>
</main>
</body>
</html>
```